Brochure Brightwell Hearth Partners

Brochure 12 x 9 tri fold with insert/ Rack card 9x4. Brightwell Hearth Partners 318 Corvane Street Easton, MD 21629410-822-2207AgingAtHomeSolution.com Tag: Devoted to Thoughtful Household Support.
What we do: Home care agency that services higher end Clients Artsy area on the water. Taking care of seniors in their home.

Our story: Opening Brightwell Hearth Partners, Inc. is my way of making a difference in an industry that is dominated by franchises that often have their policies dictated by corporate policy-makers who are unfamiliar with local customs. My goal is to raise the level of non-medical home health care in our area by providing additional, customized training, higher wages for our care-partners and an inclusive workforce in the decision-making process when developing customized care planning for our clients. Through collaboration with the client, their family and care-partners I have learned what issues, concerns and disappointments may arise which enables me to provide a more defined solution for those in need.My goal of providing superior training required locating a nationally recognized curriculum that would serve our clients’ needs. I found the perfect fit with Norla Vance’s, Kindred Pathway Method™ and her Shifting Stones Series™. These programs provide our care-partners with the tools needed to handle the challenges of natural aging and living with Dementia. I was so impressed with these programs, I became a Certified Independent Trainer; one of five in the State of Maryland. There is a bonus for our care-partners who are required to maintain Continuing Education Units - these programs qualify for credit! Improving our industry by providing exemplary care-partners is my goal!I look forward to assisting you with your needs! Dana Prewitt Owner

Services: Companion Care Service - Conversation and Companionship , Meal Preparation, Light House Keeping, Errand Service ,Grocery Shopping ,Incidental Transportation, Laundry & Linen Washing, Medication Reminders, Recreational Activities ,
Personal Care Services: Bathing ,Mobility ,Transferring & Positioning ,Incontinence Care ,Oral Hygiene ,Feeding, Toileting ,Grooming & Dressing, Special Diet Preparation.

Our Commitment to You: Extensive Care-Partner Education - We provide, in addition to state mandated training, eight additional hours of hands-on Dementia training from a Certified, Independent Instructor on the “Kindred Pathway Method” by Norla Vance, a nationally recognized instructor on aging.

Nutrition/Local Chef Inspired Training ;We provide six, two-hour food preparation sessions for our care-partners using local chefs, their recipes and locally grown food.

Meaningful & Engaging Activities - We provide a monthly list with local activities to our care-partners based on our client’s interest and capabilities. Focusing on what our client loved to do in the past.

Home Solutions When Needed; We provide management services to help keep our clients in their homes by working with current contractors or locating new ones to properly maintain a safe-living environment.

About owner: Dana Prewitt, owner of Brightwell Hearth Partners, has earned her certification as an Independent Trainer in the Kindred Pathway; Method (KPM) by Norla Vance, a nationally recognized instructor on natural aging and aging with Dementia. Dana is one of five certified independent trainers in the state of Maryland. All staff will have eight hours of hands on Dementia Kindred Pathway Method training.

On the insert 11x 4.25 want the top to be sticking out of the tri -fold "Dementia Experts . I would like to have shades of each STONE as it progresses
The Shifting STONES(R): The STONES model recognizes the dynamic nature of the human brain and its abilities. Unlike other cognitive models, it acknowledges that everyone’s abilities can change in a moment. Modifying environments, situations, interactions, and expectations will create either supportive positive opportunities or result in distress and a sense of failure. Just as gemstones need different settings and care to show their best characteristics, so do people. Rather than focusing on a person’s loss when there is brain change, seeing individuals as precious, unique, and capable encourages a care partnership and is the core of this model. Providing supportive settings for everyone, including care providers, allows them to use what they have to be their best. The STONES® advocate that everyone living with brain change when given the opportunity will shine. Norla Vance and Kindred Pathway Method

Sapphire ~ True Blue ~ Optimal Cognition, Healthy Brain•
True to self: personal preferences remain basically the same
• Can be flexible in thinking and appreciate multiple perspectives
• Stress/pain/fatigue may trigger Diamond state: back to Sapphire with relief
• Able to suppress and filter personal reactions: chooses effective responses
• Selects from options and can make informed decisions
• Processes well and able to successfully transition
• Aging doesn’t change ability: processing slows, more effort/time/practice needed
My brain is healthy - true blue. If I am aging normally or distressed, it may be hard for me to find words. I can describe what I am thinking so you understand. I may talk to myself because I am giving myself cues and prompts. I can learn new things and change habits, but it takes time and effort. Honoring my choices and preferences, when possible, is important. I need more time to make decisions. Give me the details and let me think about it before you need an answer. I am able to remember plans and information but supports are helpful. I may like specific prompts such as notes, calendars, and reminder calls. Health changes in vision, hearing, balance, coordination, depression, anxiety, pain, or medication may impact my behavior, but my cognitive abilities remain the same.

Diamond ~ Clear and Sharp ~ Routines and Rituals Rule
• Displays many facets: behavior and perspective can shift dramatically
• Prefers the familiar and may resist change: challenged by transitions
• More rigid and self-focused; sees wants as needs, when stressed
• Personal likes/dislikes in relationships/space/belongings etc, become more intense
• Reacts to changes in environment; benefits from familiar; functional/forgiving
• Needs repetition and time to absorb new/different information or routines
• Trusted authority figures can help: reacts better when respect is mutual
My overall cognition is clear and sharp. When happy and supported, I am capable and shine in my abilities. When distressed, I can be cutting and rigid and may see help as a threat. I have trouble seeing other points of view and may become less aware of boundaries or more possessive about my relationships, personal space, and belongings. I have many facets so people see me differently depending on the situation. This can cause conflict among my family, friends, or care team as it’s hard to tell if I am choosing my behavior or truly have limits in my ability. I can socially engage and have good cover skills. People will vary in their awareness of what is happening to me. I want to keep habits and environments as they have always been, even if they are problematic for me or others. I am often focused on the past, personal values, or finances. I will need help to make changes in my life; it’s hard for me. I can be in a Diamond state for reasons other than dementia.

Emerald ~ Green and On the Go With a Purpose ~ Naturally Flawed
• Sees self as able and independent, with limited awareness of changes in ability
• Lives in moments of clarity mixed with periods of loss in logic/reason/perspective
• Understanding and use of language change: vague words and many repeats
• Cues and support help when getting to/from places and doing daily routines
• Awareness of time, place, and situation will not always match current reality
• Strong emotional reactions are triggered by fears, desires, or unmet needs
Needs to know what comes next: seeks guidance and assistance to fill the day
I am flawed; it is part of being a natural emerald. I tend to be focused on what I want or need in this moment and may not be aware of my own safety or changing abilities. I can chat socially, but I typically miss one out of every four words and cannot accurately follow the meaning of longer conversations. I won’t remember the details of our time together, but I will remember how your body language and tone of voice made me feel. I may hide or misplace things and believe someone has taken them. My brain will make up information to fill in the blanks, which makes you think I am lying. If you try to correct me or argue, I may become resentful or suspicious of you. I am not always rational, but I don’t want to be made to feel incompetent. My brain plays tricks on me, taking me to different times and places in my life. When I am struggling, I may tell you, “I want to go home.” To provide the help and assistance I need, you must go with my flow, use a positive, partnered approach, and modify my environment.

Amber ~ Caught in a Moment of Time ~ Caution Required
• Focused on sensation: seeks to satisfy desires and tries to avoid what is disliked
•Environment can drive actions and reactions without awareness of safety
• Visual abilities are limited: focus is on pieces or parts, not the whole picture
• What happens to or around an Amber, may cause strong and surprising reactions
• Enters others’ space and crosses boundaries attempting to meet own needs
• Has periods of intense activity: may be very curious or repetitive with objects or actions
• Care is refused or seen as threatening, due to differences in perspective and ability.
Like a particle trapped in an amber, I am caught in a moment of time. It may surprise you to see how I take in the world around me. I may not know you or see you as a whole person. I react to you based on how you look, sound, move, smell, and respond to me. I like to do simple tasks over and over and may need to repeatedly move and touch, smell, taste, take or tear items apart. While it may exhaust or frustrate you, it soothes me. I don’t recognize danger; you will have to safeguard my environment. I’m intolerant to discomfort because my mouth, hands, feet, and genitalia are highly sensitive due to changes in my nervous system. Therefore, activities like eating, taking medication, mouth care, bathing, dressing, and toileting may distress me. Please notice my reaction and stop if I am resisting. I can’t help myself and one or both of us may get hurt emotionally and/or physically. If this happens, wait a few minutes, connect with me, and try a different approach; possibly substituting one area of focus for another.

Ruby ~ Deep and Strong in Color ~ Others Stop Seeing What is Possible
• Makes use of rhythm: can usually sing, hum, pray, sway, rock, clap, and dance
• When moving can’t stop; when stopped can’t get moving: needs guidance and help
• Big, strong movements are possible, while skilled abilities are being lost
• Danger exists due to limited abilities combined with automatic actions or reactions
• Tends to miss subtle hints, but gets magnified facial expressions and voice rhythms
• Can mimic actions or motions, but will struggle to understand instructions/gestures
• Able to pick up and hold objects, and yet not know what to do with them
As the deep red of a ruby masks detail, my obvious losses make my remaining abilities harder to notice. Although my fine motor skills have become very limited, remember that I am able to move and do simple things with my hands. You will need to anticipate, identify, and respond to all of my needs, even though I may not be aware of them. Plan to create a supportive environment, help with the details of care, and structure my day. Just as a crossing guard directs traffic, you will need to guide my movements and transitions. I can rarely stop or start on my own and switching gears is a challenge. Move with me first, then use your body to show me what you want me to do next, going one step at a time. Palm-beneath-Palm™ assistance helps me to feel safe and secure and to know what to do. Danger is part of my life, due to losses in visual skills, chewing abilities, balance, and coordination. You can reduce the risks to me, but not eliminate them. I can still have moments of joy when you are able to provide what gives me pleasure.

Pearl ~ Hidden Within a Shell ~ Beautiful Moments to Behold
• Will frequently recognize familiar touches, voices, faces, aromas, and tastes• Personhood survives, although all other capabilities are minimal
• Understanding input takes time: go slow and simplify for success
• In care, first get connected by offering comfort then use careful and caring touch
• Changes in the body are profound: weight loss, immobility, systems are failing
• As protective reflexes are lost, breathing, swallowing, and moving will be difficult
Care partners benefit from learning the art of letting go rather than simply giving up
While hidden like a pearl in an oyster shell, I will still have moments when I become alert and responsive. I am near the end of my life. Moments of connection create a sense of wholeness and value between us. Use our time together not just to provide care, but to comfort and connect with me. To help me complete life well, it’s important to honor my personhood when making medical or care decisions; please don’t talk about me as though I am not still here. I respond best to familiar voices and gentle rhythmic movements. I am ruled by reflexes and will startle easily. My brain is losing its ability to control and heal my body. Be prepared to see me having difficulty breathing or swallowing. My body may no longer desire food and drink as I prepare to leave this life. I may not be able to stop living without permission from you. Your greatest gift at this time in my life is to let me know that it is okay to go.

Target Market(s)

Children of seniors, seniors , rehabilitation centers

Requirements
Must have
• Nice photos of Seniors that are happy doing thing they like to do with help (Caregivers)
• Upbeat . Positive
Nice to have
• Processional looking - but very personal, we are taking care of their love ones
Should not have
• Not to feel like a cold hospital or end of life

```html
<!DOCTYPE html>
<html lang="en">
<head>
<meta charset="utf-8">
<title>Brightwell Hearth Partners – Tri-fold Brochure and Rack Card</title>
<link href="https://fonts.googleapis.com/css2?family=Cormorant+Garamond:ital,wght@0,500;0,600;0,700;1,600&family=Open+Sans:wght@400;600&display=swap" rel="stylesheet">
<style>
  :root{
    --bg:#c4c4c7;
    --navy:#262d72;
    --deep:#1f2560;
    --blue:#1b5f9b;
    --teal:#2a8fc3;
    --sky:#4fb0dc;
    --ink:#2b2f55;
    --text:#3a3a48;
    --paper:#fbfaf7;
    --white:#ffffff;
    --serif:"Cormorant Garamond", Georgia, serif;
    --sans:"Open Sans", Arial, sans-serif;
  }
  *{box-sizing:border-box;margin:0;padding:0}
  html,body{width:1200px;height:1194px;overflow:hidden}
  body{background:var(--bg);font-family:var(--sans);color:var(--text);position:relative}

  .spread{position:absolute;width:760px;height:570px;display:flex;box-shadow:0 6px 18px rgba(0,0,0,.18)}
  .spread--outside{left:30px;top:18px}
  .spread--inside{left:30px;top:606px}
  .panel{position:relative;width:253.33px;height:100%;overflow:hidden}

  .footer-band{position:absolute;left:0;right:0;bottom:0;height:30px;background:var(--navy);
    color:var(--white);font-size:9px;letter-spacing:.3px;display:flex;align-items:center;justify-content:center}
  .footer-band::before{content:"";position:absolute;left:0;right:0;top:-7px;height:7px;
    background:linear-gradient(90deg,var(--teal),var(--sky) 60%,transparent 60.5%)}
  .footer-band span{position:relative}

  .photo{display:block}

  /* Our Story */
  .story{background:linear-gradient(180deg,var(--paper),#f3f1ec);padding:30px 20px 40px}
  .story__title{font-family:var(--serif);font-weight:600;font-size:27px;color:var(--navy);margin-bottom:10px}
  .story__body{font-size:7.5px;line-height:1.42;text-align:justify;margin-bottom:7px}
  .story__sign{font-size:8px;line-height:1.3;margin-top:8px}

  /* Middle outside panel */
  .intro{background:linear-gradient(180deg,var(--blue) 0%,#22428a 45%,var(--deep) 100%);color:var(--white);text-align:center;padding:36px 20px 0}
  .intro__tag{font-family:var(--serif);font-size:15px;line-height:1.2;font-weight:500}
  .intro__lede{font-family:var(--serif);font-size:10.5px;line-height:1.3;margin:12px 8px 0;opacity:.92}
  .intro__photo{width:150px;height:150px;border-radius:50%;margin:18px auto 0;
    background:radial-gradient(circle at 40% 40%,#f2ede4,#cdd8de 55%,#9db4c4)}
  .intro__name{font-family:var(--serif);font-weight:600;font-size:25px;line-height:1.05;margin-top:26px}
  .intro__address{font-family:var(--serif);font-size:11px;line-height:1.35;margin-top:20px;opacity:.95}

  /* Cover */
  .cover{background:linear-gradient(180deg,#ffffff,#f4f3f0);text-align:center;padding-top:34px}
  .logo-name{font-family:var(--serif);font-weight:600;color:var(--navy);line-height:1.05}
  .cover .logo-name{font-size:27px;padding:0 16px}
  .cover__welcome{font-family:var(--serif);font-size:11.5px;color:var(--ink);margin-top:14px;line-height:1.25}
  .cover__phone{font-family:var(--serif);font-size:15px;color:var(--teal);font-weight:600;margin-top:4px}
  .cover__tag{font-family:var(--serif);font-size:15px;color:var(--navy);font-weight:600;line-height:1.15;margin:4px 18px 0}
  .cover__photo{position:absolute;left:0;right:0;bottom:30px;height:250px;
    background:linear-gradient(180deg,rgba(255,255,255,0) 0%,#e9ddd3 22%,#d9c1b0 55%,#c9a896 100%)}

  /* Rack card */
  .rack{position:absolute;left:850px;top:30px;width:250px;height:560px;overflow:hidden;
    background:linear-gradient(180deg,#ffffff,#f3f2ee);text-align:center;padding-top:38px;box-shadow:0 6px 18px rgba(0,0,0,.18)}
  .rack .logo-name{font-size:27px;padding:0 16px}
  .rack .cover__photo{height:270px}

  /* Services */
  .services{background:linear-gradient(180deg,var(--blue) 0%,#22428a 50%,var(--deep) 100%);color:var(--white)}
  .services__head{height:52px;display:flex;align-items:center;padding-left:26px;
    font-family:var(--serif);font-weight:600;font-size:25px}
  .services__photo{height:148px;background:linear-gradient(180deg,#b6785e 0%,#c9a990 45%,#6f8f58 100%);
    border-bottom-left-radius:50% 22px;border-bottom-right-radius:50% 22px}
  .services__body{padding:14px 20px 0 30px}
  .services__group{font-family:var(--serif);font-weight:700;font-size:14px;margin:6px 0 3px}
  .services__list{list-style:none;margin-bottom:10px}
  .services__list li{font-size:9.6px;line-height:1.5;position:relative;padding-left:14px}
  .services__list li::before{content:"";position:absolute;left:0;top:5px;width:5px;height:5px;border-radius:50%;background:var(--sky)}

  /* Commitment */
  .commit{background:var(--white);padding:26px 18px 40px 20px}
  .commit__title{font-family:var(--serif);font-weight:600;font-size:23px;color:var(--navy);line-height:1.05;margin-bottom:12px}
  .commit__item{display:flex;gap:8px;align-items:center;margin-bottom:13px}
  .commit__copy{flex:1}
  .commit__head{font-family:var(--serif);font-style:italic;font-weight:600;font-size:11.5px;color:var(--teal);margin-bottom:3px}
  .commit__text{font-size:7.4px;line-height:1.4}
  .commit__disc{flex:none;width:56px;height:56px;border-radius:50%}
  .disc--badge{background:#dfe6f0;border:3px solid var(--navy)}
  .disc--food{background:radial-gradient(circle,#7d4a7a,#5d8a3a)}
  .disc--activity{background:radial-gradient(circle,#f1ede6,#b9c4cc)}
  .disc--home{background:radial-gradient(circle,#e8b23a,#8c5a3a)}

  /* About Owner */
  .about{background:linear-gradient(180deg,#ffffff,#f1f1f1)}
  .about__photo{height:165px;background:linear-gradient(135deg,#f4f4f2 0%,#e8c9b3 45%,#9bb66c 100%)}
  .about__title{position:absolute;left:20px;top:20px;font-family:var(--serif);font-weight:600;font-size:23px;color:var(--navy)}
  .about__body{padding:14px 20px 0 22px}
  .about__text{font-size:7.6px;line-height:1.45;text-align:justify}
  .about__head{font-family:var(--serif);font-style:italic;font-weight:600;font-size:12px;color:var(--teal);margin:14px 0 4px}
  .about__logo{display:flex;align-items:center;gap:8px;margin-top:30px}
  .about__logo .logo-name{font-size:20px;text-align:left}
  .about__dot{width:22px;height:22px;border-radius:50%;background:var(--sky);flex:none}
  .about .footer-band{font-family:var(--serif);font-size:15px;font-weight:600;justify-content:flex-end;padding-right:22px}
</style>
</head>
<body>

<!-- Outside of tri-fold -->
<section class="spread spread--outside">
  <article class="panel story">
    <h2 class="story__title">Our Story</h2>
    <p class="story__body">Opening Brightwell Hearth Partners, Inc. is my way of making a difference in an industry that is dominated by franchises that often have their policies dictated by corporate policy-makers who are unfamiliar with local customs. My goal is to raise the level of non-medical home health care in our area by providing additional, customized training, higher wages for our care-partners and an inclusive workforce in the decision-making process when developing customized care planning for our clients. Through collaboration with the client, their family and care-partners I have learned what issues, concerns and disappointments may arise which enables me to provide a more defined solution for those in need.</p>
    <p class="story__body">My goal of providing superior training required locating a nationally recognized curriculum that would serve our clients’ needs. I found the perfect fit with Norla Vance’s, Kindred Pathway Method™ and her Shifting Stones Series™. These programs provide our care-partners with the tools needed to handle the challenges of natural aging and living with Dementia. I was so impressed with these programs, I became a Certified Independent Trainer; one of five in the State of Maryland. There is a bonus for our care-partners who are required to maintain Continuing Education Units - these programs qualify for credit! Improving our industry by providing exemplary care-partners is my goal!</p>
    <p class="story__body">I look forward to assisting you with your needs!</p>
    <p class="story__sign">Dana Prewitt<br>Owner</p>
    <div class="footer-band"><span>brightwellhearthpartners.example</span></div>
  </article>

  <article class="panel intro">
    <p class="intro__tag">Devoted to Thoughtful<br>Household Support.</p>
    <p class="intro__lede">Home care agency that services higher end Clients. Taking care of seniors in their home.</p>
    <div class="photo intro__photo" role="img" aria-label="Photo of a smiling senior woman sharing a drink with her caregiver"></div>
    <p class="intro__name">Brightwell<br>Hearth Partners</p>
    <p class="intro__address">Brightwell Hearth Partners<br>318 Corvane Street<br>Easton, MD 21774<br>410-555-0148<br>BrightwellHearthPartners.example</p>
  </article>

  <article class="panel cover">
    <p class="logo-name">Brightwell<br>Hearth Partners</p>
    <p class="cover__welcome">Welcome to<br>Brightwell Hearth Partners</p>
    <p class="cover__phone">410-555-0148</p>
    <p class="cover__tag">Devoted to Thoughtful<br>Household Support.</p>
    <div class="photo cover__photo" role="img" aria-label="Photo of a young caregiver hugging a smiling senior woman"></div>
    <div class="footer-band"><span>brightwellhearthpartners.example</span></div>
  </article>
</section>

<!-- Rack card -->
<aside class="rack">
  <p class="logo-name">Brightwell<br>Hearth Partners</p>
  <p class="cover__welcome">Welcome to<br>Brightwell Hearth Partners</p>
  <p class="cover__phone">410-555-0148</p>
  <p class="cover__tag">Devoted to Thoughtful<br>Household Support.</p>
  <div class="photo cover__photo" role="img" aria-label="Photo of a young caregiver hugging a smiling senior woman"></div>
  <div class="footer-band"><span>brightwellhearthpartners.example</span></div>
</aside>

<!-- Inside of tri-fold -->
<section class="spread spread--inside">
  <article class="panel services">
    <h2 class="services__head">Services</h2>
    <div class="photo services__photo" role="img" aria-label="Photo of a senior woman with a walker and her caregiver outside a brick house"></div>
    <div class="services__body">
      <h3 class="services__group">Companion Care Service</h3>
      <ul class="services__list">
        <li>Conversation &amp; Companionship</li>
        <li>Meal Preparation</li>
        <li>Light House Keeping</li>
        <li>Errand Service</li>
        <li>Grocery Shopping</li>
        <li>Incidental Transportation</li>
        <li>Laundry &amp; Linen Washing</li>
        <li>Medication Reminders</li>
        <li>Recreational Activities</li>
      </ul>
      <h3 class="services__group">Personal Care Services</h3>
      <ul class="services__list">
        <li>Bathing</li>
        <li>Mobility</li>
        <li>Transferring &amp; Positioning</li>
        <li>Incontinence Care</li>
        <li>Oral Hygiene</li>
        <li>Feeding</li>
        <li>Toileting</li>
        <li>Grooming &amp; Dressing</li>
        <li>Special Diet Preparation</li>
      </ul>
    </div>
  </article>

  <article class="panel commit">
    <h2 class="commit__title">Our Commitment<br>to You</h2>
    <div class="commit__item">
      <div class="commit__copy">
        <h3 class="commit__head">Extensive Care-Partner Education</h3>
        <p class="commit__text">We provide, in addition to state mandated training, eight additional hours of hands-on Dementia training from a Certified, Independent Instructor on the “Kindred Pathway Method” by Norla Vance, a nationally recognized instructor on aging.</p>
      </div>
      <div class="commit__disc disc--badge" role="img" aria-label="Trainer certification badge"></div>
    </div>
    <div class="commit__item">
      <div class="commit__copy">
        <h3 class="commit__head">Nutrition/Local Chef Inspired Training</h3>
        <p class="commit__text">We provide six, two-hour food preparation sessions for our care-partners using local chefs, their recipes and locally grown food.</p>
      </div>
      <div class="commit__disc disc--food" role="img" aria-label="Photo of fresh local vegetables"></div>
    </div>
    <div class="commit__item">
      <div class="commit__copy">
        <h3 class="commit__head">Meaningful &amp; Engaging Activities</h3>
        <p class="commit__text">We provide a monthly list with local activities to our care-partners based on our client’s interest and capabilities. Focusing on what our client loved to do in the past.</p>
      </div>
      <div class="commit__disc disc--activity" role="img" aria-label="Photo of a senior man painting"></div>
    </div>
    <div class="commit__item">
      <div class="commit__copy">
        <h3 class="commit__head">Home Solutions When Needed</h3>
        <p class="commit__text">We provide management services to help keep our clients in their homes by working with current contractors or locating new ones to properly maintain a safe-living environment.</p>
      </div>
      <div class="commit__disc disc--home" role="img" aria-label="Photo of a hard hat and tool belt"></div>
    </div>
    <div class="footer-band"><span>brightwellhearthpartners.example</span></div>
  </article>

  <article class="panel about">
    <div class="photo about__photo" role="img" aria-label="Photo of a young hand resting on an elderly hand"></div>
    <h2 class="about__title">About Owner</h2>
    <div class="about__body">
      <p class="about__text">Dana Prewitt, owner of Brightwell Hearth Partners, has earned her certification as an Independent Trainer in the Kindred Pathway Method (KPM) by Norla Vance, a nationally recognized instructor on natural aging and aging with Dementia. Dana is one of five certified independent trainers in the state of Maryland. All staff will have eight hours of hands on Dementia Kindred Pathway Method training.</p>
      <h3 class="about__head">No two companies are alike!</h3>
      <p class="about__text">We provide our care-partners with the tools needed to handle the challenges of natural aging and living with Dementia / Alzheimer. Most seniors would rather be home instead of in a facility.</p>
      <div class="about__logo">
        <span class="about__dot"></span>
        <p class="logo-name">Brightwell Hearth Partners</p>
      </div>
    </div>
    <div class="footer-band"><span>410-555-0148</span></div>
  </article>
</section>

</body>
</html>
```